A Modern & Sleek "Coming Soon" Page for an A.I Recruiting App

For the “Coming Soon” website, a simple background with no people in it. I've attached an A.I image of what the page should generally look like.

- A single mobile phone as the main focus where the user actually clicks on the, “notify me” button (after entering their email address).
- In the background where the pillars/columns are seen in the example, should be subtle pad locks that are in their opened position with a key inside the lock. I've attached images to try to illustrate this idea, but they are far away in style from what I'm looking for.

SLOGAN: Unlocking the power of meaningful connections
LOGO/TITLE: Should be the name as shown in image with only the name "KelvoLink" on it
COLORS: Purplish/blue hues. Should not be too feminine
NOTE: The user should only click once when signing up/entering their email.

Product: A recruiting platform that matches employers/employees with A.I. and prioritizing cultural fit/values system before skills. The industry we are tackling first is the caregiving industry (nannies, tutors, elderly). All users will be background screened and that info lives on the blockchain. All users will have the option to review and be reviewed/rated.

```html
<!DOCTYPE html>
<html lang="en">
<head>
<meta charset="utf-8">
<title>KelvoLink — Coming Soon</title>
<link rel="stylesheet" href="https://fonts.googleapis.com/css2?family=Roboto:wght@300;400;700&display=swap">
<style>
  :root {
    --ink-deep: #1a0b27;
    --violet-dark: #2b1242;
    --violet-mid: #4a2470;
    --lavender: #8e62b6;
    --lavender-light: #b48ad6;
    --magenta: #b0278e;
    --phone-body: #1c0a2a;
    --phone-screen: #4b1f6e;
    --lock-tone: #a35ad8;
    --white: #ffffff;
  }
  * { margin: 0; padding: 0; box-sizing: border-box; }
  html, body { width: 1200px; height: 804px; overflow: hidden; }
  body {
    font-family: "Roboto", Arial, sans-serif;
    color: var(--white);
    background: var(--ink-deep);
    position: relative;
  }
  .hero {
    position: absolute; left: 0; top: 0; width: 1200px; height: 725px;
    overflow: hidden;
  }
  .hero-scene {
    position: absolute; inset: 0;
    background:
      radial-gradient(ellipse 520px 360px at 330px 420px, rgba(142,98,182,0.30), transparent 70%),
      linear-gradient(180deg, var(--violet-dark) 0%, #35164f 45%, var(--violet-mid) 72%, var(--lavender) 88%, var(--lavender-light) 100%);
  }
  .lock-visual {
    position: absolute; left: 34px; top: 240px; width: 250px; height: 350px;
    border-radius: 45% 45% 48% 48%;
    background: radial-gradient(ellipse at 45% 65%, var(--lock-tone), rgba(163,90,216,0.35) 60%, transparent 75%);
  }
  .phone-visual {
    position: absolute; left: 285px; top: 127px; width: 250px; height: 493px;
    transform: rotate(-7.5deg);
    border-radius: 38px;
    background: var(--phone-body);
    padding: 10px;
    box-shadow: 0 18px 40px rgba(10,0,20,0.55);
  }
  .phone-visual .screen {
    width: 100%; height: 100%; border-radius: 30px;
    background: linear-gradient(170deg, #6a2c93 0%, var(--phone-screen) 45%, #2e1145 100%);
  }

  .site-logo {
    position: absolute; left: 58px; top: 34px;
    font-weight: 300; font-size: 36px; letter-spacing: 5.5px;
    line-height: 1; color: var(--white);
  }
  .menu-toggle {
    position: absolute; left: 1111px; top: 36px; width: 40px; height: 28px;
    display: flex; flex-direction: column; justify-content: space-between;
  }
  .menu-toggle span { display: block; height: 3px; background: var(--white); border-radius: 2px; }

  .phone-title {
    position: absolute; left: 300px; top: 257px; width: 200px;
    text-align: center; font-weight: 700; font-size: 26px; letter-spacing: 0.5px; line-height: 32px;
  }
  .phone-slogan {
    position: absolute; left: 313px; top: 317px; width: 200px;
    text-align: center; font-size: 14px; line-height: 22px; font-weight: 400;
  }
  .btn-notify {
    position: absolute; left: 367px; top: 447px; width: 136px; height: 51px;
    border: 2px solid var(--white); border-radius: 26px;
    display: flex; align-items: center; justify-content: center;
    font-weight: 700; font-size: 16px; letter-spacing: 0.3px; color: var(--white);
  }

  .headline {
    position: absolute; left: 598px; top: 214px;
    font-weight: 300; font-size: 80px; letter-spacing: 15px; line-height: 1;
    color: var(--magenta);
  }
  .slogan {
    position: absolute; left: 599px; top: 313px;
    font-size: 24px; font-weight: 400; color: var(--white);
  }
  .btn-signup {
    position: absolute; left: 600px; top: 381px; width: 137px; height: 53px;
    border-radius: 27px; background: var(--magenta);
    display: flex; align-items: center; justify-content: center;
    font-weight: 700; font-size: 16px; letter-spacing: 0.3px; color: var(--white);
  }

  .site-footer {
    position: absolute; left: 0; top: 725px; width: 1200px; height: 79px;
    background: var(--ink-deep);
    display: flex; align-items: center; justify-content: center;
    font-weight: 700; font-size: 16px; letter-spacing: 0.3px;
  }
  .site-footer .divider { margin: 0 15px; }
</style>
</head>
<body>
  <section class="hero">
    <div class="hero-scene" role="img" aria-label="Purple 3D stage with soft curved pillars in the background"></div>
    <div class="lock-visual" role="img" aria-label="Opened purple padlock with a key inside"></div>
    <div class="phone-visual" role="img" aria-label="Smartphone standing on the stage"><div class="screen"></div></div>

    <div class="site-logo">KELVOLINK</div>
    <div class="menu-toggle" aria-label="Menu"><span></span><span></span><span></span></div>

    <p class="phone-title">KELVOLINK</p>
    <p class="phone-slogan">Unlocking the power of<br>meaningful connections</p>
    <a class="btn-notify">NOTIFY ME</a>

    <h1 class="headline">KELVOLINK</h1>
    <p class="slogan">Unlocking the power of meaningful connections</p>
    <a class="btn-signup">SIGN UP</a>
  </section>

  <footer class="site-footer">
    <span>©COPYRIGHTS 2024 KELVOLINK</span><span class="divider">|</span><span>ALL RIGHTS RESERVED</span>
  </footer>
</body>
</html>
```